Business Card for Coastal Tundrabridge Advisory

We need a business card for Coastal Tundrabridge Advisory. The company website address is provided below. The company logo is attached. We provide specialized permafrost services to the mining, transportation, and oil & gas industries. The card should be prepared for:
Matthias Korhonen, PhD.
Coastal Tundrabridge Advisory
PO Box 418259
Quillwater, Alaska 99642
Direct: +1-907-555-0143
Email: mkorhonen@tundrabridgeadvisory.example
Website: www.coastaltundrabridgeadvisory.example

```html
<!DOCTYPE html>
<html lang="en">
<head>
<meta charset="utf-8">
<title>Coastal Tundrabridge Advisory – Business Card</title>
<link href="https://fonts.googleapis.com/css2?family=Roboto:wght@300;400;500;700&display=swap" rel="stylesheet">
<style>
  :root {
    --stage: #262626;
    --card: #111722;
    --card-edge: #0b0f17;
    --ink: #ffffff;
    --ink-soft: #d9dde3;
    --emboss: #1a2230;
    --ice-blue: #2b6f9e;
    --ice-deep: #16324a;
  }
  * { box-sizing: border-box; margin: 0; padding: 0; }
  html, body {
    width: 1200px; height: 780px; overflow: hidden;
    background: var(--stage);
    font-family: "Roboto", Arial, sans-serif;
    color: var(--ink);
  }
  .stage {
    width: 1200px; height: 780px;
    display: flex; align-items: center; justify-content: center; gap: 40px;
  }
  .card {
    position: relative;
    width: 540px; height: 309px;
    background: var(--card);
    overflow: hidden;
    box-shadow: 0 18px 40px rgba(0,0,0,.45);
  }

  /* Front */
  .card-front .corner-tab {
    position: absolute; top: 0; right: 26px;
    width: 30px; height: 14px; background: var(--ink);
  }
  .card-front .company-name {
    position: absolute; left: 30px; top: 40px; width: 230px;
    font-size: 23px; font-weight: 500; line-height: 1.15;
    color: var(--ink); letter-spacing: .5px;
  }
  .card-front .person {
    position: absolute; right: 26px; top: 26px; text-align: right;
  }
  .person-name { font-size: 24px; line-height: 1.1; }
  .person-name .first { font-weight: 700; }
  .person-name .last { font-weight: 300; }
  .person-title { font-size: 13px; font-weight: 700; margin-top: 2px; }

  .card-front .faint-name {
    position: absolute; right: 26px; bottom: 84px; width: 250px; text-align: right;
    font-size: 26px; font-weight: 500; line-height: 1.1;
    color: var(--emboss);
  }

  .contact {
    position: absolute; left: 30px; bottom: 24px;
    font-size: 12.5px; font-weight: 400; color: var(--ink-soft); line-height: 1.45;
  }
  .contact .address { margin-bottom: 10px; }
  .contact-line { display: flex; align-items: center; gap: 8px; }
  .contact-line svg { width: 12px; height: 12px; flex: none; }

  /* Back */
  .card-back .pattern {
    position: absolute; inset: 0;
    background: linear-gradient(120deg, var(--ice-deep) 0%, #132537 35%, var(--card) 70%, #0e141e 100%);
  }
  .card-back .company-name {
    position: absolute; left: 300px; top: 80px;
    font-size: 14px; font-weight: 500; color: var(--ink); line-height: 1.15; width: 160px;
  }
  .services {
    position: absolute; left: 0; right: 0; bottom: 28px; text-align: center;
  }
  .services-heading { font-size: 13px; font-weight: 700; letter-spacing: .3px; }
  .services-text { font-size: 11.5px; font-weight: 400; margin-top: 4px; color: var(--ink-soft); }
</style>
</head>
<body>
<main class="stage">

  <section class="card card-front" aria-label="Business card front">
    <div class="corner-tab"></div>
    <p class="company-name">Coastal Tundrabridge Advisory</p>

    <div class="person">
      <p class="person-name"><span class="first">Matthias</span> <span class="last">Korhonen</span></p>
      <p class="person-title">PhD</p>
    </div>

    <p class="faint-name" aria-hidden="true">Coastal Tundrabridge Advisory</p>

    <div class="contact">
      <p class="address">PO Box 418259<br>Quillwater, Alaska 99642</p>
      <p class="contact-line">
        <svg viewBox="0 0 12 12" aria-hidden="true"><path d="M3 1.2 4.6 3.5 3.6 4.6c.6 1.5 2 2.9 3.8 3.8l1.1-1 2.3 1.6-.9 1.8C6.5 10.6 1.4 5.5 1.2 2.1Z" fill="currentColor"/></svg>
        +1-907-555-0143
      </p>
      <p class="contact-line">
        <svg viewBox="0 0 12 12" aria-hidden="true"><rect x="1" y="2.5" width="10" height="7" fill="none" stroke="currentColor"/><path d="M1 2.8 6 6.6l5-3.8" fill="none" stroke="currentColor"/></svg>
        mkorhonen@tundrabridgeadvisory.example
      </p>
      <p class="contact-line">
        <svg viewBox="0 0 12 12" aria-hidden="true"><circle cx="6" cy="6" r="4.8" fill="none" stroke="currentColor"/><ellipse cx="6" cy="6" rx="2" ry="4.8" fill="none" stroke="currentColor"/><path d="M1.2 6h9.6" stroke="currentColor"/></svg>
        www.coastaltundrabridgeadvisory.example
      </p>
    </div>
  </section>

  <section class="card card-back" aria-label="Business card back">
    <div class="pattern" role="img" aria-label="Repeating company name pattern in blue and dark tones"></div>
    <p class="company-name">Coastal Tundrabridge Advisory</p>
    <div class="services">
      <p class="services-heading">OUR SERVICES</p>
      <p class="services-text">We provide specialized permafrost services to the mining, transportation, and oil &amp; gas industries</p>
    </div>
  </section>

</main>
</body>
</html>
```